Brackenford Air Business Card Design

Design new, 2 sides, business cards for a residential and light commercial heating, air conditioning contractor.

Target Market(s)

Homeowners, small businesses

Industry/Entity Type

Business

Contact Information for Business Card

Dominic Westerhall
Phone - 862-415-2736
Email
Address - PO box 518
Brightwater NJ 07912
Website - www.HarborBreezeLLC.example

Requirements
Must have
• logo, company colors, standard size with no die cut, so I can use nova stamp

```html
<!DOCTYPE html>
<html lang="en">
<head>
<meta charset="utf-8">
<title>Brackenford Air Business Card</title>
<link rel="stylesheet" href="https://fonts.googleapis.com/css2?family=Open+Sans:ital,wght@0,400;0,700;1,400&display=swap">
<style>
  :root {
    --backdrop: #e6e6e6;
    --card: #ffffff;
    --brand-red: #9b1b30;
    --brand-orange: #f0a020;
    --ink: #1c1c1c;
  }
  * { box-sizing: border-box; margin: 0; padding: 0; }
  html, body { width: 1200px; height: 1058px; overflow: hidden; }
  body {
    background: var(--backdrop);
    font-family: "Open Sans", Arial, sans-serif;
    color: var(--ink);
    position: relative;
  }
  .card {
    position: absolute;
    left: 283px;
    width: 634px;
    height: 363px;
    background: var(--card);
  }
  .card--front { top: 140px; }
  .card--back { top: 560px; display: flex; align-items: center; justify-content: center; }

  .holder { position: absolute; left: 48px; top: 80px; }
  .holder__name {
    font-weight: 700; font-size: 21px; letter-spacing: 0.3px;
    color: var(--brand-red); text-transform: uppercase; line-height: 26px;
  }
  .holder__title {
    font-weight: 700; font-size: 15px; color: var(--brand-orange); line-height: 20px;
  }
  .divider {
    position: absolute; left: 49px; top: 137px;
    width: 523px; height: 3px; background: var(--brand-red);
  }

  .address { position: absolute; left: 48px; top: 188px; font-size: 16px; line-height: 22px; font-style: normal; }
  .services { position: absolute; left: 48px; top: 235px; font-size: 16px; font-style: italic; line-height: 25px; }

  .contacts {
    position: absolute; right: 40px; top: 190px;
    list-style: none; font-size: 15.5px; line-height: 24.5px; text-align: right;
  }
  .contacts li { display: flex; align-items: center; justify-content: flex-end; gap: 10px; }
  .contacts svg { width: 15px; height: 15px; fill: var(--brand-red); flex: none; }

  .wordmark { display: flex; align-items: center; gap: 14px; }
  .wordmark__dot { width: 20px; height: 20px; background: var(--brand-orange); border-radius: 50%; }
  .wordmark__name {
    font-weight: 700; font-size: 40px; color: var(--brand-red);
    text-transform: uppercase; letter-spacing: 1px; white-space: nowrap;
  }
</style>
</head>
<body>
  <section class="card card--front" aria-label="Business card front">
    <div class="holder">
      <p class="holder__name">Dominic Westerhall</p>
      <p class="holder__title">CEO/Founder</p>
    </div>
    <div class="divider"></div>

    <address class="address">
      PO box 518<br>
      Brightwater NJ 07912
    </address>
    <p class="services">
      Residential &amp;<br>
      light commercial heating<br>
      Air conditioning contractor
    </p>

    <ul class="contacts">
      <li>862 415 2736
        <svg viewBox="0 0 16 16" aria-hidden="true"><path d="M3.5 1.5l2.5 0 1 3.5-1.6 1.2c.8 1.8 2.2 3.2 4 4l1.2-1.6 3.4 1v2.6c0 .7-.6 1.3-1.3 1.3C6.9 13.5 2.2 8.8 2.2 2.8c0-.7.6-1.3 1.3-1.3z"/></svg>
      </li>
      <li>862 415 2790
        <svg viewBox="0 0 16 16" aria-hidden="true"><path d="M4.5 0.5h7c.6 0 1 .4 1 1v13c0 .6-.4 1-1 1h-7c-.6 0-1-.4-1-1v-13c0-.6.4-1 1-1zM5 2.5v10h6v-10zM7 13.3h2v1H7z"/></svg>
      </li>
      <li>862 415 2741
        <svg viewBox="0 0 16 16" aria-hidden="true"><path d="M4 1h8v4H4zM1.5 6h13c.6 0 1 .4 1 1v5h-3v3h-9v-3h-3V7c0-.6.4-1 1-1zM5 11v3h6v-3z"/></svg>
      </li>
      <li>dominic@brackenfordair.example
        <svg viewBox="0 0 16 16" aria-hidden="true"><path d="M1 3h14v1.2L8 8.5 1 4.2zM1 5.8l7 4.3 7-4.3V13H1z"/></svg>
      </li>
      <li>www.BrackenfordAirLLC.example
        <svg viewBox="0 0 16 16" aria-hidden="true"><circle cx="8" cy="8" r="7"/><path d="M5 4.5c1.5.3 2 1.5 1.2 2.5-.7.8.2 2 1.3 2.2.8.2.8 1.6.2 2.8" stroke="#fff" stroke-width="1.3" fill="none"/></svg>
      </li>
    </ul>
  </section>

  <section class="card card--back" aria-label="Business card back">
    <div class="wordmark">
      <span class="wordmark__dot"></span>
      <span class="wordmark__name">Brackenford Air</span>
    </div>
  </section>
</body>
</html>
```